UI design for an Zyn(Halvo) photo editing app

This design contest is to design the UI/screenshots of an Zyn(Halvo) app named "Kestrel Pix". Some minor design details are left out at this point as the mockup is still in progress. The icon of this app will be designed separately. The winner of this job will be selected to work on a long term basis as an Dorvo version and several updates will have to be designed as well as the Quillex version. Please take
this as a long term opportunity.
The photo app is called "Kestrel Pix". The design need to dynamic, different that stands out WITH a serious and polished look.
All the mockups and sample screenshots are attached for ease. Please thoroughly review them.
This app has the following screens:
1. Welcome screen(just a simple background will do now as icon will be put later).
2. Main Screen (or LightBox)
The background of this screen can be the same as the background of the welcome screen. It can be a wooden background OR a background of your
choice that fits and blends in the buttons and fonts/colors.
The main screen has this bars/buttons/options that has separate screens:
On top, menu bar:
has these buttons
settings on the left(icon)
in the middle, 3 buttons (please check lightbox mockup and lightbox sample pics)
on the right, share icon(check share screen sample)
Our share options:
"Share" button screenshot:
Our share options:
Save
Email
Copy
Moodlefy
Chatterbay
Zorbly
Quorra
in the middle, just background where the pictures would appear later after importing
or saving
at the bottom bar:
3 buttons:
Camera Roll(on the left)
Camera Button(middle)
Advanced Button(on the right)
2 versions of this screenshot need to be designed.
1. regular version with all the options
2. regular version plus the "steam effect" button showing up on top of the "Advanced" button(mockup with red lines)
3 separate screenshots need to be designed for the options"
settings screenshot(please check sample):
Gift Kestrel Pix to a friend
Rate/review in the Tundle Hub
(space in between...so they are grouped)
Geotagiing(on/off)
Captured photos get location-specific information(these lines in smaller fonts)
Launch in Capture Mode(on/off)
Kestrel Pix is automatically lauched in camera mode
Autosave to Camera Roll(on/off)
Captured photos are directly saved to camera roll
Reset All Tutorials
Tap to reset all the tutorials
In the "Steam Effect" screen, please check the mockup
Top Bar: lightbox button(to go back), heading and Done button
Middle: Steam background(provided)
Bottom bar:
refresh button
droplets(when clicked on/off options show up on top, please check mockup)
finger size(when clicked 3 options show up)
steam density(when clicked 3 options show up)
Please use the buttons for the droplets, finger size and steam density from the steam effects button image provided)
(and also the background of this screenshot(in the middle) would be a steam screen which is provided. Please use the
steam background provided and you need to use the background in the middle, just omit the top and the bottom bar from the image)
Now back to the main(lightbox screen):
When Clicked on the "Camera" in the middle of the bottom bar, the capture mode screen shows up.
Please refer to the mockup first
There you will see the cancel button on the left
camera button in the middle
a small settings button on the right
and a filters button on the right
and the filters bar on the top
ours need to like this
please refer to capture mode sample 1
please refer to capture mode sample 2
please refer to capture mode sample 3
normal
Grid
timer(5/15/30 secs)
Edit Screen(check sample)
Edit options
Adjust:(displayed on a bar)
1. Left
2. Right
3. Horizontal
4. Vertical
5. Straightening
Crop:
None
Original
Golden
Freeform
Square
3:2
4:3
4:6
5:7
8:10
16:9
Filters:(please note that this filter icon and the filter icon in the "capture mode" screenshot need to same)
(the filters are displayed on a bar, please check sample)
There is a sample picture that you need to put in the picture of the filters. It would be same picture in
every filter at this point.
00.None
0.Calibrate
1. aurora
2. drizzle
3. icicle
4. blizzard
5. calm
6. dew
7. knot
8. dry
9. eye
10. flurry
11. fog
12. frost
13. hail
14. haze
15. heat
16. humid
17. overcast
18. polar
19. thermal
20. trace
Editing options on top:(check sample)
Brightness
Contrast
Saturation
Textures:(dispalyed on a bar, check sample)
1.None
2.Bark
3.Grunge1
4.Grunge2
5.grunge3
6.Grunge4
7.Paper
8.Cardboard
9.Wood
10.Bokeh
11.Bricks
12.Metal
13.Asphalt
14.Pavement1
15.Pavement2
16.Paint1
17.Paint2
18.Rust
19.Towel
20.Stone1
21.Stone2
22.Wall
23.Urban1
24.Urban2
25.Urban3
26.Watercolor
Tilt-shift/Vignette:(check sample)
Borders:(check samples, at this point, we are working on them, you just need to make a bar that displays them)
1.None
2.
3.
4.
5.
6.
7.
8.
9.
10.
11.
12.
13.
14.
15.
16.
This is our primary design mockup. Upon selecting the final version, we will be working on some more and minor details(as
we are also working with the coders).
And there is a folder callled "app sample". Please take a look at it and think how our app can be different and stand out.
Thanks and feel free to contact me anytime if you have any questions. Looking forward to hearing from you and building a long term
relationship.
All camera app users who likes to edit their photos with cool tools.
Building

```html
<!DOCTYPE html>
<html lang="en">
<head>
<meta charset="utf-8">
<title>Kestrel Pix – Capture Timer</title>
<link rel="stylesheet" href="https://fonts.googleapis.com/css2?family=Open+Sans:wght@600;700;800&display=swap">
<style>
  :root{
    --bar-red:#b11c1f;
    --bar-red-dark:#7e1013;
    --ring-pink:#e9a3a6;
    --ring-bright:#ffd9dc;
    --ring-line:#2a2022;
    --core-black:#0c0d10;
    --text-light:#e6ebf0;
    --label-steel:#a9b7c6;
    --track-red:#c71c22;
    --track-bg:#eef0f2;
  }
  *{margin:0;padding:0;box-sizing:border-box}
  html,body{width:676px;height:1200px;overflow:hidden;background:#222}
  body{font-family:"Open Sans",sans-serif}
  .screen{position:relative;width:640px;height:1136px;transform:scale(1.05625);transform-origin:0 0;overflow:hidden}
  .camera-feed{position:absolute;left:0;top:0;width:640px;height:1020px;
    background:linear-gradient(160deg,#8d8478 0%,#c9c6bd 22%,#6d6a66 45%,#3b3a3c 68%,#1f2023 100%)}
  .timer-dial{position:absolute;left:0;top:0;width:640px;height:1020px}
  .timer-value{position:absolute;left:235px;top:425px;width:200px;text-align:center;color:var(--text-light);font-weight:800;font-size:118px;line-height:1;text-shadow:0 3px 6px #000}
  .timer-unit{position:absolute;left:235px;top:545px;width:200px;text-align:center;color:var(--text-light);font-weight:700;font-size:30px;letter-spacing:1px;text-shadow:0 2px 4px #000}
  .timer-status{position:absolute;left:0;top:788px;width:616px;text-align:center;color:var(--text-light);font-weight:700;font-size:31px;letter-spacing:.5px;text-shadow:0 2px 3px #000}
  .zoom-control{position:absolute;left:30px;top:910px;width:575px;height:36px}
  .zoom-label{position:absolute;left:3px;top:5px;color:var(--text-light);font-weight:700;font-size:19px;text-shadow:0 1px 2px #000}
  .zoom-track{position:absolute;left:65px;top:4px;width:508px;height:26px;border-radius:13px;background:var(--track-bg);box-shadow:inset 0 1px 3px rgba(0,0,0,.5)}
  .zoom-fill{position:absolute;left:163px;top:5px;width:335px;height:16px;border-radius:0 8px 8px 0;background:var(--track-red)}
  .zoom-thumb{position:absolute;left:154px;top:1px;width:16px;height:24px;border-radius:4px;background:linear-gradient(#fff,#b9bec4);border:1px solid #777}
  .toolbar{position:absolute;left:0;top:1020px;width:640px;height:116px;background:linear-gradient(var(--bar-red),var(--bar-red-dark));border-top:2px solid #6d0c0f}
  .toolbar::before{content:"";position:absolute;left:0;right:0;top:6px;border-top:2px dashed rgba(255,200,200,.45)}
  .cancel-button{position:absolute;left:30px;top:32px;width:82px;height:45px;border-radius:8px;background:linear-gradient(#fdfdfd,#c9cbce);color:var(--bar-red-dark);font-weight:700;font-size:19px;display:flex;align-items:center;justify-content:center;box-shadow:0 2px 3px rgba(0,0,0,.5)}
  .toolbar-icon{position:absolute}
</style>
</head>
<body>
<main class="screen">
  <div class="camera-feed" role="img" aria-label="Live camera viewfinder showing an office desk with a laptop and phone"></div>

  <svg class="timer-dial" viewBox="0 0 640 1020" aria-hidden="true">
    <defs>
      <radialGradient id="ringGlow" cx="50%" cy="50%" r="50%">
        <stop offset="62%" stop-color="#b84a52" stop-opacity=".75"/>
        <stop offset="100%" stop-color="#f1b9bc" stop-opacity=".9"/>
      </radialGradient>
      <radialGradient id="coreGloss" cx="45%" cy="30%" r="70%">
        <stop offset="0%" stop-color="#8b8f96"/>
        <stop offset="45%" stop-color="#2c2e33"/>
        <stop offset="100%" stop-color="#050506"/>
      </radialGradient>
      <linearGradient id="titleFill" x1="0" y1="0" x2="0" y2="1">
        <stop offset="0%" stop-color="#dfe8f1"/>
        <stop offset="100%" stop-color="#8a9bb0"/>
      </linearGradient>
      <path id="titleArc" d="M105 297 A300 300 0 0 1 565 297"/>
    </defs>
    <circle cx="335" cy="490" r="222" fill="none" stroke="url(#ringGlow)" stroke-width="106"/>
    <path d="M277.5 275.6 A222 222 0 0 1 549.4 432.5" fill="none" stroke="var(--ring-bright)" stroke-width="106" opacity=".95"/>
    <g stroke="var(--ring-line)" stroke-width="3">
      <line x1="335" y1="320" x2="335" y2="215" transform="rotate(15 335 490)"/>
      <line x1="335" y1="320" x2="335" y2="215" transform="rotate(45 335 490)"/>
      <line x1="335" y1="320" x2="335" y2="215" transform="rotate(75 335 490)"/>
      <line x1="335" y1="320" x2="335" y2="215" transform="rotate(105 335 490)"/>
      <line x1="335" y1="320" x2="335" y2="215" transform="rotate(135 335 490)"/>
      <line x1="335" y1="320" x2="335" y2="215" transform="rotate(165 335 490)"/>
      <line x1="335" y1="320" x2="335" y2="215" transform="rotate(195 335 490)"/>
      <line x1="335" y1="320" x2="335" y2="215" transform="rotate(225 335 490)"/>
      <line x1="335" y1="320" x2="335" y2="215" transform="rotate(255 335 490)"/>
      <line x1="335" y1="320" x2="335" y2="215" transform="rotate(285 335 490)"/>
      <line x1="335" y1="320" x2="335" y2="215" transform="rotate(315 335 490)"/>
      <line x1="335" y1="320" x2="335" y2="215" transform="rotate(345 335 490)"/>
    </g>
    <circle cx="335" cy="490" r="168" fill="var(--core-black)" opacity=".9"/>
    <circle cx="335" cy="490" r="122" fill="url(#coreGloss)"/>
    <path d="M548 503 L578 503 L563 519 Z" fill="var(--track-red)"/>
    <text font-family="Open Sans, sans-serif" font-weight="800" font-size="54" fill="url(#titleFill)" stroke="#b3373d" stroke-width="2" letter-spacing="3">
      <textPath href="#titleArc" startOffset="50%" text-anchor="middle">Set Timer</textPath>
    </text>
  </svg>

  <div class="timer-value">5</div>
  <div class="timer-unit">SEC.</div>
  <div class="timer-status">Timer Active</div>

  <div class="zoom-control">
    <span class="zoom-label">1.5x</span>
    <div class="zoom-track"><div class="zoom-fill"></div><div class="zoom-thumb"></div></div>
  </div>

  <nav class="toolbar">
    <div class="cancel-button">Cancel</div>
    <svg class="toolbar-icon" style="left:255px;top:4px" width="80" height="80" viewBox="0 0 80 80" aria-label="Capture">
      <g fill="none" stroke="#f4f4f4" stroke-width="5">
        <rect x="6" y="20" width="68" height="50" rx="10"/>
        <path d="M26 20 L30 9 H50 L54 20"/>
        <circle cx="40" cy="45" r="16"/>
        <circle cx="40" cy="45" r="7"/>
      </g>
    </svg>
    <svg class="toolbar-icon" style="left:433px;top:34px" width="46" height="46" viewBox="0 0 46 46" aria-label="Filters">
      <circle cx="23" cy="23" r="20" fill="#e8e8e8"/>
      <g stroke="var(--bar-red)" stroke-width="3">
        <line x1="23" y1="3" x2="28" y2="20"/><line x1="43" y1="23" x2="26" y2="28"/>
        <line x1="23" y1="43" x2="18" y2="26"/><line x1="3" y1="23" x2="20" y2="18"/>
      </g>
      <circle cx="23" cy="23" r="6" fill="var(--bar-red)"/>
    </svg>
    <svg class="toolbar-icon" style="left:567px;top:33px" width="46" height="46" viewBox="0 0 46 46" aria-label="Settings">
      <g fill="#f0f0f0">
        <circle cx="23" cy="23" r="15"/>
        <rect x="19" y="1" width="8" height="44" rx="2"/>
        <rect x="19" y="1" width="8" height="44" rx="2" transform="rotate(45 23 23)"/>
        <rect x="19" y="1" width="8" height="44" rx="2" transform="rotate(90 23 23)"/>
        <rect x="19" y="1" width="8" height="44" rx="2" transform="rotate(135 23 23)"/>
      </g>
      <circle cx="23" cy="23" r="7" fill="var(--bar-red)"/>
    </svg>
  </nav>
</main>
</body>
</html>
```